Agriculture Security Company needs a business card design

We need a business card design for a new company based in Seattle calls Ferncrest Guardline LLC. We provide high-end physical security solutions that is geared and focused towards to the marijuana grow operations, wholesalers and distributors. We DO NOT get involved in the retail operations (store fronts). We would like to see designs that incorporate professionalism, reliability, trustworthy and forward thinking as traits of our organization.

Industry/Entity Type

Security

```html
<!DOCTYPE html>
<html lang="en">
<head>
<meta charset="utf-8">
<title>Ferncrest Guardline LLC — Business Card</title>
<link rel="stylesheet" href="https://fonts.googleapis.com/css2?family=Open+Sans:wght@400;600;700&display=swap">
<style>
  :root {
    --canvas-bg: #ece9e4;
    --card-bg: #ffffff;
    --card-edge: #f3f3f3;
    --green-dark: #2e7d3a;
    --green-light: #7cb342;
    --text-grey: #4a4a4a;
    --shadow: rgba(0, 0, 0, 0.18);
  }
  * { margin: 0; padding: 0; box-sizing: border-box; }
  html, body {
    width: 1200px; height: 1023px; overflow: hidden;
    background: var(--canvas-bg);
    font-family: "Open Sans", Arial, sans-serif;
  }
  .stage { position: relative; width: 1200px; height: 1023px; }
  .card {
    position: absolute;
    width: 520px; height: 300px;
    top: 361px;
    overflow: hidden;
    background: linear-gradient(135deg, var(--card-bg) 0%, var(--card-edge) 100%);
    box-shadow: 0 10px 30px var(--shadow);
  }
  .card--front { left: 60px; }
  .card--back  { left: 620px; }

  .brand-name {
    font-family: "Open Sans", Arial, sans-serif;
    font-weight: 700;
    color: var(--green-dark);
    letter-spacing: 0.5px;
    display: flex; align-items: center; gap: 8px;
  }
  .brand-dot { width: 12px; height: 12px; border-radius: 50%; background: var(--green-dark); flex: none; }

  .card--front .brand-name {
    position: absolute; left: 36px; top: 130px; font-size: 30px;
  }

  .contact { position: absolute; left: 290px; top: 40px; width: 210px; }
  .person-name { font-size: 24px; font-weight: 700; color: var(--green-dark); line-height: 1.2; }
  .person-title { font-size: 13px; color: var(--green-light); line-height: 1.4; }
  .divider {
    width: 300px; height: 2px;
    margin: 10px 0 10px -90px;
    background: linear-gradient(90deg, rgba(46,125,58,0) 0%, var(--green-dark) 60%, rgba(46,125,58,0.2) 100%);
  }
  .company { font-size: 12.5px; font-weight: 600; color: var(--green-dark); line-height: 1.5; }
  .address { font-size: 12px; color: var(--text-grey); line-height: 1.5; }
  .details { list-style: none; margin-top: 12px; }
  .details li {
    font-size: 12px; color: var(--text-grey); line-height: 1.7;
    display: flex; align-items: center; gap: 8px;
  }
  .details svg { width: 12px; height: 12px; fill: var(--green-dark); flex: none; }

  .card--back .brand-name {
    position: absolute; left: 0; right: 0; top: 128px; justify-content: center; font-size: 36px;
  }
  .back-url {
    position: absolute; left: 18px; top: 30px;
    writing-mode: vertical-rl;
    font-size: 11px; letter-spacing: 2px; color: var(--green-light);
    white-space: nowrap;
  }
</style>
</head>
<body>
<main class="stage">
  <section class="card card--front" aria-label="Business card front">
    <div class="brand-name"><span class="brand-dot"></span>Ferncrest</div>
    <div class="contact">
      <p class="person-name">Dana Whitlow</p>
      <p class="person-title">President</p>
      <div class="divider"></div>
      <p class="company">Ferncrest Guardline LLC</p>
      <p class="address">2718 Cedar Row Ave<br>Seattle, WA 98101</p>
      <ul class="details">
        <li><svg viewBox="0 0 24 24" aria-hidden="true"><path d="M6.6 10.8a15.1 15.1 0 0 0 6.6 6.6l2.2-2.2a1 1 0 0 1 1-.25 11.4 11.4 0 0 0 3.6.57 1 1 0 0 1 1 1V20a1 1 0 0 1-1 1A17 17 0 0 1 3 4a1 1 0 0 1 1-1h3.5a1 1 0 0 1 1 1c0 1.25.2 2.45.57 3.57a1 1 0 0 1-.25 1z"/></svg>555-014-2290</li>
        <li><svg viewBox="0 0 24 24" aria-hidden="true"><path d="M2 5h20v14H2z"/><path d="M2 5l10 8 10-8" fill="none" stroke="#ffffff" stroke-width="2"/></svg>info@ferncrestguardline.com</li>
        <li><svg viewBox="0 0 24 24" aria-hidden="true"><circle cx="12" cy="12" r="10"/></svg>www.ferncrestguardline.com</li>
      </ul>
    </div>
  </section>

  <section class="card card--back" aria-label="Business card back">
    <p class="back-url">www.ferncrestguardline.com</p>
    <div class="brand-name"><span class="brand-dot"></span>Ferncrest</div>
  </section>
</main>
</body>
</html>
```